Steady Hands, professional newsletter for GAPM

** updated based on results so far** We need a 2 page newsletter designed on both sides of an 8.6 x 11 sheet back and front. Page one needs our logo below, name steady hands in large letters tagline of official newsletter of the guild of acute practice medicine volume and issue number locations It needs to include five locations for 250-400 word articles each with a spot for a picture. Page 2 needs to include contact information including address, phone number, email, twitter and facebook info below. The design need to complement out log in color, be professional with clean lines and easy to follow. We are a non profit organization dedicated to providers of urgent care medicine.

Target Market(s)

Physicians, Nurse Practitioners, Physician Assistants

Requirements
Must have
• 2 pages, back and front 8.5x 11
• 5 article area 250-400 words, one image for each
• our logo
• Name: Steady Hands - page one large visible print
• Contact inf:
• Guild of Acute Practice Medicine
• 912 Larkmoor Ave. Suite 418E
• Harlow Springs, IL 60719
• 1 855-314-7093
• Info@gaopm.org
• @GuildAPM
Nice to have
• ease of entering info
• professional clean lines

```html
<!DOCTYPE html>
<html lang="en">
<head>
<meta charset="utf-8">
<title>Steady Hands — Newsletter</title>
<link rel="stylesheet" href="https://fonts.googleapis.com/css2?family=Open+Sans:wght@400;600;700;800&family=Oswald:wght@500&display=swap">
<style>
  :root {
    --orange: #eda63a;
    --gold: #e7a630;
    --rust: #d0592a;
    --red: #c2402c;
    --blue: #3d78b8;
    --ink: #555;
    --grey: #7a7a7a;
    --dark: #2b2b2b;
    --bg: #e6e6e6;
    --white: #ffffff;
  }
  * { box-sizing: border-box; margin: 0; padding: 0; }
  html, body { width: 1200px; height: 927px; overflow: hidden; }
  body { background: var(--bg); font-family: "Open Sans", Arial, sans-serif; position: relative; }

  .page { position: absolute; top: 101px; width: 560px; height: 725px; background: var(--white); overflow: hidden; box-shadow: 0 6px 18px rgba(0,0,0,.18); }
  .page--front { left: 25px; }
  .page--back { left: 615px; }

  /* Front page */
  .masthead-band { height: 26px; background: var(--orange); display: flex; justify-content: space-between; align-items: center; padding: 0 32px; color: var(--white); font-size: 9px; font-weight: 700; letter-spacing: .6px; }
  .masthead-title { text-align: center; color: var(--rust); font-weight: 800; font-size: 60px; letter-spacing: 1px; line-height: 1; margin-top: 12px; }
  .brand { display: flex; align-items: center; justify-content: center; gap: 8px; margin-top: 8px; }
  .brand__mark { width: 26px; height: 26px; border-radius: 50%; background: var(--rust); }
  .brand__rule { width: 1px; height: 40px; background: var(--rust); }
  .brand__name { font-variant: small-caps; color: var(--grey); font-size: 12px; line-height: 1.05; letter-spacing: .5px; }
  .tagline-band { position: relative; height: 18px; margin-top: 12px; }
  .tagline-band svg { position: absolute; inset: 0; }
  .tagline-band span { position: relative; display: block; padding-left: 75px; line-height: 18px; color: var(--white); font-size: 8.5px; font-weight: 700; letter-spacing: .2px; }

  .articles { padding: 10px 26px 0 28px; color: var(--ink); font-size: 8.5px; line-height: 1.36; }
  .article__title { font-size: 11px; font-weight: 600; color: #444; margin: 6px 0 7px; }
  .article p { margin-bottom: 10px; text-align: justify; }
  .article__lead { display: flex; gap: 12px; }
  .article__lead .col { flex: 1; }
  .placeholder { flex: 0 0 232px; height: 232px; margin-top: 18px; background: var(--blue); color: var(--white); display: flex; flex-direction: column; align-items: center; justify-content: center; }
  .placeholder strong { font-size: 19px; font-weight: 700; }
  .placeholder small { font-size: 11px; opacity: .8; }
  .foot-band { position: absolute; left: 0; right: 0; bottom: 0; height: 12px; }

  /* Back page */
  .back-art { position: absolute; inset: 0; }
  .page--back .brand { position: absolute; top: 58px; left: 24px; justify-content: flex-start; margin: 0; }
  .page--back .brand__mark { width: 30px; height: 30px; }
  .page--back .brand__rule { height: 48px; }
  .page--back .brand__name { font-size: 14px; }
  .contact { position: absolute; top: 200px; left: 0; right: 0; text-align: center; color: var(--white); font-style: normal; font-size: 10px; font-weight: 600; line-height: 1.35; }
  .contact__label { font-size: 11.5px; margin-bottom: 14px; }
  .contact p { margin-bottom: 12px; }
  .org-title { position: absolute; top: 528px; left: 0; right: 0; text-align: center; font-family: "Oswald", "Arial Narrow", sans-serif; font-weight: 500; color: var(--rust); font-size: 38px; line-height: 1.35; }
  .site-bar { position: absolute; left: 0; right: 0; bottom: 0; height: 84px; background: var(--dark); color: var(--gold); font-weight: 700; font-size: 23px; display: flex; align-items: center; justify-content: center; letter-spacing: .5px; }
</style>
</head>
<body>

<section class="page page--front">
  <header>
    <div class="masthead-band"><span>VOLUME - 01 | ISSUE - 001</span><span>WWW. GAOPM.ORG</span></div>
    <h1 class="masthead-title">STEADY HANDS</h1>
    <div class="brand">
      <span class="brand__mark"></span>
      <span class="brand__rule"></span>
      <span class="brand__name">Guild of<br>Acute Practice<br>Medicine</span>
    </div>
    <div class="tagline-band">
      <svg viewBox="0 0 560 18" preserveAspectRatio="none">
        <polygon points="0,0 560,0 560,18 0,18" fill="var(--orange)"/>
        <polygon points="500,0 560,0 560,18 455,18" fill="var(--red)"/>
      </svg>
      <span>OFFICIAL NEWSLETTER OF THE GUILD OF ACUTE PRACTICE MEDICINE</span>
    </div>
  </header>

  <main class="articles">
    <article class="article">
      <h2 class="article__title">THIS IS DUMMY TITLE 01 GENERATED</h2>
      <div class="article__lead">
        <div class="col">
          <p>Lorem ipsum dolor sit amet, consectetuer adipiscing elit. Aenean commodo ligula eget dolor. Aenean massa. Cum sociis natoque penatibus et magnis dis parturient montes, nascetur ridiculus mus.</p>
          <p>Donec quam felis, ultricies nec, pellentesque eu, pretium quis, sem. Nulla consequat massa quis enim. Donec pede justo, fringilla vel, aliquet nec, vulputate eget, arcu. In enim justo, rhoncus ut, imperdiet a, venenatis vitae, justo. Nullam dictum felis eu pede mollis pretium. Integer tincidunt. Cras dapibus. Vivamus elementum semper nisi.</p>
          <p>Aenean vulputate eleifend tellus. Aenean leo ligula, porttitor eu, consequat vitae, eleifend ac, enim. Aliquam lorem ante, dapibus in, viverra quis, feugiat a, tellus. Phasellus viverra nulla ut metus varius laoreet. Quisque rutrum. Aenean imperdiet. Etiam ultricies nisi vel augue. Curabitur ullamcorper ultricies nisi. Nam eget dui. Etiam rhoncus. Maecenas tempus, tellus eget condimentum rhoncus, sem quam semper libero, sit amet adipiscing sem neque sed ipsum. Nam quam nunc, blandit vel, luctus pulvinar, hendrerit id, lorem. Maecenas nec odio et ante tincidunt tempus.</p>
        </div>
        <div class="placeholder" role="img" aria-label="Article photo area">
          <strong>Placeholder Image</strong>
          <small>Lorem Ipsum</small>
        </div>
      </div>
      <p>Donec vitae sapien ut libero venenatis faucibus. Nullam quis ante. Etiam sit amet orci eget eros faucibus tincidunt. Duis leo. Sed fringilla mauris sit amet nibh. Donec sodales sagittis magna. Sed consequat, leo eget bibendum sodales, augue velit cursus nunc, quis gravida magna mi a libero. Fusce vulputate eleifend sapien. Vestibulum purus quam, scelerisque ut, mollis sed, nonummy id, metus. Nullam accumsan lorem in dui. Cras ultricies mi eu turpis hendrerit fringilla. Vestibulum ante ipsum primis in faucibus orci luctus et ultrices posuere cubilia Curae; In ac dui quis mi.</p>
    </article>
    <article class="article">
      <h2 class="article__title">THIS IS DUMMY TITLE 02 GENERATED</h2>
      <p>Lorem ipsum dolor sit amet, consectetuer adipiscing elit. Aenean commodo ligula eget dolor. Aenean massa. Cum sociis natoque penatibus et magnis dis parturient montes, nascetur ridiculus mus. Donec quam felis, ultricies nec, pellentesque eu, pretium quis, sem. Nulla consequat massa quis enim. Donec pede justo, fringilla vel, aliquet nec, vulputate eget, arcu. In enim justo, rhoncus ut, imperdiet a, venenatis vitae, justo. Nullam dictum felis eu pede mollis pretium. Integer tincidunt. Cras dapibus.</p>
      <p>Vivamus elementum semper nisi. Aenean vulputate eleifend tellus. Aenean leo ligula, porttitor eu, consequat vitae, eleifend ac, enim. Aliquam lorem ante, dapibus in, viverra quis, feugiat a, tellus. Phasellus viverra nulla ut metus varius laoreet. Quisque rutrum. Aenean imperdiet. Etiam ultricies nisi vel augue. Curabitur ullamcorper ultricies nisi. Nam eget dui. Etiam rhoncus. Maecenas tempus, tellus eget condimentum rhoncus, sem quam semper libero, sit amet adipiscing sem neque sed ipsum.</p>
    </article>
  </main>

  <svg class="foot-band" viewBox="0 0 560 12" preserveAspectRatio="none">
    <rect width="560" height="12" fill="var(--orange)"/>
    <polygon points="385,12 397,0 560,0 560,12" fill="var(--red)"/>
  </svg>
</section>

<section class="page page--back">
  <svg class="back-art" viewBox="0 0 560 725" preserveAspectRatio="none" aria-hidden="true">
    <path d="M0,560 C150,508 380,474 560,460 L560,470 C380,482 150,515 0,572 Z" fill="#e9b86a"/>
    <path d="M0,555 C150,502 380,468 560,455 L560,462 C380,476 150,510 0,565 Z" fill="var(--red)"/>
    <path d="M0,143 C200,140 400,110 560,50 L560,455 C380,466 150,498 0,553 Z" fill="var(--gold)"/>
  </svg>

  <div class="brand">
    <span class="brand__mark"></span>
    <span class="brand__rule"></span>
    <span class="brand__name">Guild of<br>Acute Practice<br>Medicine</span>
  </div>

  <address class="contact">
    <div class="contact__label">ADDRESS:</div>
    <p>912 Larkmoor Ave. Suite 418E<br>Harlow Springs, IL 60719</p>
    <p>PHONE: 1 855-314-7093</p>
    <p>eMAIL: INFO@GAOPM.ORG</p>
    <p>www.twitter.com/GuildAPM<br>www.facebook.com/Acute-Practice-Guild-of-Physicians-572910348816402/</p>
  </address>

  <h2 class="org-title">GUILD OF<br>ACUTE PRACTICE MEDICINE</h2>

  <div class="site-bar">WWW.GAOPM.ORG</div>
</section>

</body>
</html>
```